Lorvex Tilo medical cannibis cultivation company

tag - Tilo rise
Lorvex Tilo medical cannabis cultivation - logo is selected- can we please see bold examples with our selection. We are mainly dealing with medical companies and professionals. We would like to be stand out in the crowd with our designs. Welcome any and all attempts. Thanks

Target Market(s)

Medical and Professional

Industry/Entity Type

Medical And Science

Font styles to use
Sans Serif

Colors

Designer to choose colors to be used in the design.

Requirements
Must have
• Bright colour and be bold- Love the teal and magenta that is currently on the dark background design.
Nice to have
• shading and the 3D affect- The shadowed appearance.
Should not have
• Anything related to illegal activity or un professional manners

```html
<!DOCTYPE html>
<html lang="en">
<head>
<meta charset="utf-8">
<title>Lorvex Tilo – Business Card</title>
<link href="https://fonts.googleapis.com/css2?family=Roboto:wght@400;500;700&display=swap" rel="stylesheet">
<style>
  :root {
    --backdrop: #e4e4e4;
    --card: #050505;
    --teal: #1aa9e0;
    --magenta: #9b3f98;
    --grey: #8e9297;
    --text: #e6e6e6;
    --divider: #3a3a3a;
    --glow: rgba(255, 255, 255, 0.28);
  }
  * { margin: 0; padding: 0; box-sizing: border-box; }
  html, body { width: 1125px; height: 1200px; overflow: hidden; }
  body {
    background: radial-gradient(ellipse at center, #ececec 0%, var(--backdrop) 60%, #d6d6d6 100%);
    font-family: "Roboto", Arial, sans-serif;
    position: relative;
  }
  .card {
    position: absolute;
    left: 150px;
    width: 826px;
    height: 470px;
    background: linear-gradient(160deg, #0d0d0d 0%, var(--card) 45%, #000 100%);
    border-radius: 30px;
    box-shadow:
      0 2px 3px rgba(0, 0, 0, 0.35),
      0 22px 40px rgba(0, 0, 0, 0.28),
      inset 0 1px 0 rgba(255, 255, 255, 0.08);
  }
  .card--front { top: 98px; }
  .card--back { top: 631px; }

  .brand {
    position: absolute;
    display: flex;
    flex-direction: column;
    align-items: center;
  }
  .card--front .brand { left: 70px; width: 340px; top: 266px; }
  .card--back .brand { left: 243px; width: 340px; top: 282px; }
  .brand__row { display: flex; align-items: center; gap: 14px; }
  .brand__dot {
    width: 26px; height: 26px; border-radius: 50%;
    background: var(--magenta);
  }
  .brand__name {
    font-weight: 500;
    font-size: 44px;
    line-height: 52px;
    color: var(--teal);
    letter-spacing: 0.5px;
    white-space: nowrap;
  }
  .brand__tag {
    display: flex; align-items: center; gap: 8px;
    margin-top: 2px;
    font-size: 19px;
    letter-spacing: 2px;
    color: var(--grey);
    text-transform: uppercase;
  }
  .brand__tag::before, .brand__tag::after {
    content: ""; width: 58px; height: 1.5px; background: var(--grey);
  }

  .divider {
    position: absolute;
    left: 450px; top: 75px;
    width: 2px; height: 265px;
    background: linear-gradient(to bottom, transparent, var(--divider) 20%, var(--divider) 80%, transparent);
  }

  .contact {
    position: absolute; left: 495px; top: 88px; color: var(--text);
    text-shadow: 0 0 4px var(--glow), 1px 2px 2px rgba(0, 0, 0, 0.9);
  }
  .contact__name { font-size: 29px; font-weight: 700; color: var(--magenta); line-height: 1.1; }
  .contact__role { font-size: 20px; font-weight: 500; color: var(--teal); margin-top: 2px; }
  .contact__address { font-size: 19px; line-height: 25px; margin-top: 16px; }
  .contact__list { list-style: none; margin-top: 14px; }
  .contact__item {
    display: flex; align-items: center; gap: 12px;
    font-size: 19px; line-height: 26px;
  }
  .contact__icon { width: 18px; height: 18px; flex: none; fill: var(--magenta); }

  .website {
    position: absolute;
    left: 0; right: 0; top: 408px;
    text-align: center;
    font-size: 20px;
    letter-spacing: 9px;
    color: var(--text);
    text-shadow: 0 0 4px var(--glow);
  }
</style>
</head>
<body>

<section class="card card--front">
  <div class="brand">
    <div class="brand__row">
      <span class="brand__dot"></span>
      <span class="brand__name">Lorvex Tilo</span>
    </div>
    <div class="brand__tag">Tilo rise</div>
  </div>

  <div class="divider"></div>

  <div class="contact">
    <p class="contact__name">MARA QUELL</p>
    <p class="contact__role">CEO/FOUNDER</p>
    <p class="contact__address">2914 Birchwood Lane<br>Kellridge, Norvale 58210</p>
    <ul class="contact__list">
      <li class="contact__item">
        <svg class="contact__icon" viewBox="0 0 24 24"><path d="M6.6 10.8a15 15 0 0 0 6.6 6.6l2.2-2.2c.3-.3.7-.4 1-.2 1.1.4 2.3.6 3.6.6.6 0 1 .4 1 1V20c0 .6-.4 1-1 1A17 17 0 0 1 3 4c0-.6.4-1 1-1h3.5c.6 0 1 .4 1 1 0 1.3.2 2.5.6 3.6.1.3 0 .7-.2 1z"/></svg>
        555 204 7731
      </li>
      <li class="contact__item">
        <svg class="contact__icon" viewBox="0 0 24 24"><path d="M8 1h8a2 2 0 0 1 2 2v18a2 2 0 0 1-2 2H8a2 2 0 0 1-2-2V3a2 2 0 0 1 2-2zm0 3v14h8V4zm4 15.5a1 1 0 1 0 0 2 1 1 0 0 0 0-2z"/></svg>
        555 318 6642
      </li>
      <li class="contact__item">
        <svg class="contact__icon" viewBox="0 0 24 24"><path d="M7 3h10v5H7zM4 9h16a2 2 0 0 1 2 2v7h-4v3H6v-3H2v-7a2 2 0 0 1 2-2zm4 7v3h8v-3z"/></svg>
        555 907 2145
      </li>
      <li class="contact__item">
        <svg class="contact__icon" viewBox="0 0 24 24"><path d="M3 5h18a1 1 0 0 1 1 1v12a1 1 0 0 1-1 1H3a1 1 0 0 1-1-1V6a1 1 0 0 1 1-1zm1 2.5V17h16V7.5l-8 5z"/></svg>
        mara@lorvextilo.com
      </li>
    </ul>
  </div>

  <p class="website">www.lorvextilorise.com</p>
</section>

<section class="card card--back">
  <div class="brand">
    <div class="brand__row">
      <span class="brand__dot"></span>
      <span class="brand__name">Lorvex Tilo</span>
    </div>
    <div class="brand__tag">Tilo rise</div>
  </div>
</section>

</body>
</html>
```